High-end Oceanfront Real Estate Group Needs Clean, Modern Web Design

I’m looking for a clean, professional, modern and beautiful homepage web design for a Real Estate group in Southern California, USA.

The group/company is “Marwick on the Shore,” and they specialize in high end (i.e. expensive), oceanfront real estate in the Orange County area.

The look and feel of the page should accentuate the brand qualities: luxurious/expensive, professional, and beautiful (Orange County is one of the most beautiful areas in all the US and we would love the site to emphasize the beautiful beaches and scenery it has to offer).

Looks we like:
• www.brantleyhomesrealty.example
• www.closedbyvane.example -- I think the design is pretty out-dated in this site, but I like the organization/layout of the site

Header Tags (I don’t know if we can fit all of these, may need a side-menu, but I’d prefer header title only if possible):
• Welcome
• Featured Listings
• Previously Sold
• Sell
• Property Search
• Team
• Videos
• Blog
• Explore O.C.
• Contact

I have attached the beach and logo pics that we would like to use as the header, a few pictures of the team, and one sample home/view pic which can be used in any of the other sections (for pictures of the homes, just find expensive oceanfront houses and that will be fine).

I promise to provide feedback to each and every design submission. I appreciate the hard work that all of you are putting into your designs. There can be only one contest winner, but I hope to give all of you helpful feedback to submit the best designs possible!

Target Market(s)

Very wealthy home owners of oceanfront properties. These properties are worth several millions of dollars, and thus the site and brand needs to be targeted to very wealthy, successful individuals and families (both US and international buyers).

Industry/Entity Type

Real Estate

Number of Pages Required

2 page

Requirements
Must have
• I don’t want to give too many requirements, because I want to let you all be creative. However, here are the few Must Haves:
• Must submit 2 page designs (a home page and a sub page)
• Must use logo provided
• Focus is mostly on homes, but I would like to include some beach/ocean imagery as well
• The first “item” on the home page should be an accordion/slider which shows pictures of homes and with 1 line of text: “List with the Leader” and two link buttons: “Sell Your Home” and “Buy Your Home”
• Color palette needs to be mainly blues--to match ocean and sky blue
• Exported in all major formats (psd,ai,eps,png,jpeg,etc)
Nice to have
• We don’t necessarily need all of these, but would like to feature most:
• List of videos
• “Meet the Team”—brief team bios and pics
• Link(s) to Blog
• “List with the Leader” – section on why they should choose this firm
• Featured Listings
• Previously Sold

```html
<!DOCTYPE html>
<html lang="en">
<head>
<meta charset="utf-8">
<title>Marwick on the Shore — Oceanfront Real Estate</title>
<link href="https://fonts.googleapis.com/css2?family=Open+Sans:wght@300;400;600;700&family=Oswald:wght@400;500&display=swap" rel="stylesheet">
<style>
:root{
  --blue:#1f6fc5;
  --blue-dark:#17539a;
  --navy:#0f1e33;
  --ink:#222;
  --text:#555;
  --muted:#888;
  --line:#d6d6d6;
  --panel:#ececec;
  --footer:#1d1d1d;
  --footer-deep:#0e0e0e;
  --white:#fff;
}
*{box-sizing:border-box;margin:0;padding:0}
html,body{width:1200px;height:3821px;overflow:hidden}
body{font-family:"Open Sans",Arial,sans-serif;color:var(--text);background:var(--white);position:relative}
section,header,footer{position:absolute;left:0;width:1200px}
.photo{position:absolute;display:block}

/* Hero */
.hero{top:0;height:597px;background:linear-gradient(180deg,#1b2b45 0%,#24395a 35%,#3a4b5f 60%,#151c26 100%)}
.hero-glow{position:absolute;left:0;top:0;width:1200px;height:597px;background:radial-gradient(ellipse 420px 180px at 600px 300px,rgba(255,200,120,.35),rgba(255,200,120,0) 70%)}
.brand{position:absolute;left:131px;top:15px;width:162px;height:105px;display:flex;align-items:center;justify-content:center;text-align:center;color:var(--white);font-family:"Oswald",sans-serif;font-weight:400;font-size:22px;line-height:1.15;letter-spacing:1px;text-transform:uppercase}
.social-top{position:absolute;left:824px;top:22px;display:flex;gap:9px}
.social-top span{width:26px;height:26px;border-radius:50%;border:2px solid rgba(255,255,255,.85)}
.lang{position:absolute;left:979px;top:22px;width:84px;height:26px;border:1px solid rgba(255,255,255,.7);border-radius:13px;color:var(--white);font-size:11px;line-height:24px;padding-left:14px}
.lang::after{content:"";position:absolute;right:12px;top:10px;border:4px solid transparent;border-top-color:#fff}
.main-nav{position:absolute;left:409px;top:82px;display:flex;font-size:13px;color:var(--white)}
.main-nav a{color:var(--white);text-decoration:none;padding:0 13px;border-left:1px solid rgba(255,255,255,.45);line-height:16px}
.main-nav a:first-child{border-left:0;font-weight:700}
.hero-title{position:absolute;top:300px;left:0;width:1200px;text-align:center;font-family:"Oswald",sans-serif;font-weight:500;font-size:44px;color:var(--white);letter-spacing:.5px}
.hero-btn{position:absolute;top:372px;width:322px;height:64px;background:rgba(10,14,22,.72);color:var(--white);font-family:"Oswald",sans-serif;font-size:30px;white-space:nowrap;display:flex;align-items:center;justify-content:center;gap:14px}
.hero-btn svg{width:30px;height:30px;flex:none}
.btn-sell{left:245px}
.btn-buy{left:590px}
.thumbs{position:absolute;top:478px;left:131px;display:flex;gap:15px}
.thumbs .photo{position:relative;width:144px;height:107px;border:3px solid rgba(255,255,255,.8)}
.thumbs .active{border-color:#e4b04a}
.slide-arrow{position:absolute;top:514px;width:20px;height:34px}

/* Search */
.search{top:597px;height:173px;background:#f3f3f3;border-bottom:1px solid var(--line)}
.search h2{position:absolute;left:131px;top:26px;font-size:21px;font-weight:700;color:var(--blue-dark)}
.field{position:absolute;height:33px;background:var(--white);border:1px solid #c9c9c9;font-size:12px;color:#666;line-height:31px;padding-left:10px}
.field.select::after{content:"";position:absolute;right:10px;top:13px;border:5px solid transparent;border-top-color:#777}
.search .to{position:absolute;left:376px;top:128px;font-size:12px;color:#444}
.search-btn{position:absolute;left:940px;top:122px;width:126px;height:33px;background:#111;color:var(--white);font-size:13px;display:flex;align-items:center;justify-content:center;gap:8px}

/* Welcome */
.welcome{top:770px;height:260px;text-align:center}
.welcome h1{position:absolute;top:50px;width:1200px;font-size:36px;font-weight:400;color:#333}
.welcome .tag{position:absolute;top:108px;width:1200px;font-size:13px;letter-spacing:6px;color:#777}
.welcome .tag::before,.welcome .tag::after{content:"";display:inline-block;width:70px;height:1px;background:#ccc;vertical-align:middle;margin:0 14px}
.welcome p{position:absolute;left:131px;top:144px;width:938px;font-size:12.5px;line-height:22px;color:#555}

/* Featured */
.featured{top:1030px;height:382px;background:var(--panel)}
.section-title{position:absolute;width:1200px;text-align:center;font-size:27px;color:#333;font-weight:400}
.featured .section-title{top:30px}
.featured .rule{position:absolute;left:131px;top:84px;width:938px;height:1px;background:#cfcfcf}
.card{position:absolute;top:90px;width:203px;height:253px;background:var(--white);box-shadow:0 1px 3px rgba(0,0,0,.15)}
.card .photo{left:6px;top:6px;width:191px;height:118px}
.price{position:absolute;left:6px;top:104px;width:191px;height:22px;background:rgba(31,111,197,.9);color:var(--white);font-size:13px;text-align:center;line-height:22px}
.card h3{position:absolute;left:6px;top:140px;font-size:15px;color:var(--ink);font-weight:700}
.card .loc{position:absolute;left:6px;top:162px;font-size:12px;color:#666}
.card .more{position:absolute;left:0;top:214px;width:203px;height:36px;background:var(--blue);color:var(--white);font-size:14px;font-weight:700;text-align:center;line-height:36px}

/* Explore */
.explore{top:1412px;height:430px;background:linear-gradient(180deg,#1a2436 0%,#27364d 55%,#1b1f28 100%)}
.explore h2{position:absolute;top:38px;width:1200px;text-align:center;font-size:31px;font-weight:700;color:var(--white)}
.explore p{position:absolute;left:131px;top:104px;width:938px;font-size:12.5px;line-height:20px;color:#dfe6ef;text-align:center}
.explore-btn{position:absolute;left:540px;top:196px;width:120px;height:36px;border:2px solid #5aa2ef;border-radius:18px;background:var(--blue);color:var(--white);font-size:12px;font-weight:700;text-align:center;line-height:32px}
.spot{position:absolute;top:271px;width:160px;text-align:center}
.spot .tile{width:82px;height:82px;margin:0 auto;background:var(--white);border:2px solid #cfd8e4;display:flex;align-items:center;justify-content:center}
.spot .tile .photo{position:relative;width:58px;height:58px;background:var(--blue-dark);border-radius:4px}
.spot span{display:block;margin-top:14px;font-size:12px;font-weight:600;color:var(--white);line-height:16px}

/* Sold */
.sold{top:1842px;height:308px}
.sold-frame{position:absolute;left:131px;top:45px;width:938px;height:238px;border:1px solid var(--line);background:#fafafa}
.sold-tab{position:absolute;left:496px;top:33px;width:209px;height:34px;background:var(--blue);color:var(--white);font-size:14px;font-weight:700;text-align:center;line-height:34px}
.sold-item{position:absolute;top:98px;width:209px}
.sold-item .photo{position:relative;width:209px;height:130px}
.sold-item .plus{position:absolute;left:92px;top:112px;width:24px;height:24px;background:#111;color:#fff;font-size:18px;line-height:22px;text-align:center}
.sold-item .info{display:flex;justify-content:space-between;font-size:12px;font-weight:700;color:#333;margin-top:9px}
.sold-item .info b{color:var(--blue)}
.sold-item .status{margin-top:8px;height:30px;background:var(--blue);color:var(--white);text-align:center;font-size:13px;font-weight:700;line-height:30px}

/* Team */
.team{top:2150px;height:513px}
.team .section-title{top:40px;font-size:24px;font-weight:700}
.team .rule{position:absolute;left:470px;top:84px;width:260px;height:1px;background:#bbb}
.bubble{position:absolute;background:var(--white);border:1px solid #cfcfcf;border-radius:18px;box-shadow:0 1px 4px rgba(0,0,0,.08);font-size:12px;line-height:20px;color:#666;padding:24px 24px}
.bubble-left{left:218px;top:128px;width:360px;height:200px;padding-top:40px}
.bubble-right{left:590px;top:100px;width:359px;height:170px}
.avatar{position:absolute;width:92px;height:92px;border-radius:50%;border:4px solid #e2e2e2}
.member{position:absolute;font-size:17px;font-weight:700;color:#222;text-transform:uppercase}
.member small{display:block;font-size:12px;font-style:italic;font-weight:400;text-transform:none;color:#555;margin-top:2px}

/* Consult */
.consult{top:2663px;height:301px;background:#dfe7f0}
.consult-panel{position:absolute;left:0;top:0}
.consult h2{position:absolute;left:275px;top:70px;width:260px;text-align:right;font-size:20px;font-weight:400;color:var(--white)}
.consult h2 b{font-weight:700}
.consult p{position:absolute;left:160px;top:112px;width:333px;text-align:right;font-size:14px;line-height:25px;color:var(--white);text-transform:uppercase}
.consult-icon{position:absolute;left:525px;top:110px;width:66px;height:66px;border-radius:50%;background:#8a8f97;border:4px solid #fff;display:flex;align-items:center;justify-content:center}
.input{position:absolute;left:687px;width:298px;height:44px;border:1px solid rgba(255,255,255,.8);background:rgba(255,255,255,.18);color:var(--white);font-size:14px;padding:12px 10px}
.send{position:absolute;left:687px;top:261px;width:95px;height:32px;background:var(--blue);color:var(--white);font-size:14px;font-weight:700;text-align:center;line-height:32px}

/* Blog */
.blog{top:2964px;height:529px}
.blog .section-title{top:34px;font-size:24px;font-weight:700}
.blog .rule{position:absolute;left:455px;top:80px;width:290px;height:1px;background:#bbb}
.post{position:absolute;top:132px;width:298px}
.post .date{position:absolute;left:0;top:0;width:48px;height:62px;background:var(--blue);color:var(--white);text-align:center;font-size:13px;font-weight:700;line-height:20px;padding-top:10px}
.post .date b{display:block;font-size:17px}
.post .ico{position:absolute;left:0;width:48px;height:54px;background:#2a2a2a;display:flex;align-items:center;justify-content:center}
.post .photo{left:52px;top:0;width:246px;height:179px}
.post h3{position:absolute;left:52px;top:192px;font-size:14px;font-weight:700;color:#222;white-space:nowrap}
.post .meta{position:absolute;left:52px;top:216px;font-size:10px;color:#777}
.post .meta b{color:var(--blue)}
.post p{position:absolute;left:52px;top:232px;width:246px;font-size:11.5px;line-height:16px;color:#777}
.post .read{position:absolute;left:52px;top:282px;width:96px;height:28px;border-radius:14px;background:var(--blue);color:var(--white);font-size:12px;font-weight:700;text-align:center;line-height:28px}

/* Footer */
.site-footer{top:3493px;height:292px;background:var(--footer);color:#ddd}
.site-footer h4{position:absolute;font-size:16px;font-weight:700;color:var(--white)}
.links{position:absolute;top:92px;list-style:none;font-size:13px;line-height:20px;color:#ccc}
.links li::before{content:"›";color:var(--blue);margin-right:8px}
.follow{position:absolute;left:131px;top:224px;display:flex;align-items:center;gap:9px;font-size:15px;font-weight:700;color:var(--white)}
.follow span{width:24px;height:24px;border-radius:50%;background:#4a4a4a}
.video-col{position:absolute;left:445px;top:-18px;width:307px;height:310px;background:var(--footer-deep)}
.video{position:absolute;left:18px;top:106px;width:271px;height:164px}
.play{position:absolute;left:118px;top:160px;width:52px;height:38px;background:rgba(0,0,0,.8);border-radius:6px;display:flex;align-items:center;justify-content:center}
.video-bar{position:absolute;left:18px;top:256px;width:271px;height:14px;background:rgba(0,0,0,.75)}
.video-bar i{position:absolute;left:30px;top:6px;width:160px;height:3px;background:#c0392b}
.site-footer .news{position:absolute;left:812px;top:94px;width:257px;font-size:12.5px;line-height:19px;color:#ccc}
.email{position:absolute;left:812px;top:188px;width:210px;height:38px;background:var(--white);color:#888;font-size:12px;line-height:38px;padding-left:26px}
.go{position:absolute;left:1022px;top:188px;width:47px;height:38px;background:var(--blue);color:var(--white);font-size:13px;font-weight:700;text-align:center;line-height:38px}
.copyright{position:absolute;left:0;top:3785px;width:1200px;height:36px;background:var(--footer-deep);color:#aaa;text-align:center;font-size:11px;line-height:36px}
</style>
</head>
<body>

<header class="hero">
  <div class="photo" style="left:0;top:0;width:1200px;height:597px;background:linear-gradient(180deg,#1b2b45 0%,#2a3e5e 40%,#46505c 65%,#151b24 100%)" role="img" aria-label="Luxury home at dusk with lit windows and a pool terrace"></div>
  <div class="hero-glow"></div>
  <div class="brand">Marwick<br>on the<br>Shore</div>
  <div class="social-top"><span></span><span></span><span></span><span></span></div>
  <div class="lang">English</div>
  <nav class="main-nav">
    <a>Home</a><a>About us</a><a>Property Search</a><a>Team</a><a>Videos</a><a>Blog</a><a>Explore O.C</a><a>Contact</a>
  </nav>
  <h1 class="hero-title">LOOKING FOR A LUXURIOUS &amp; BEAUTIFUL HOME</h1>
  <a class="hero-btn btn-sell">SELL YOUR HOME
    <svg viewBox="0 0 30 30"><circle cx="15" cy="15" r="13" fill="none" stroke="#fff" stroke-width="2"/><path d="M12 9l6 6-6 6" fill="none" stroke="#fff" stroke-width="2.5"/></svg></a>
  <a class="hero-btn btn-buy">BUY YOUR HOME
    <svg viewBox="0 0 30 30"><circle cx="15" cy="15" r="13" fill="none" stroke="#fff" stroke-width="2"/><path d="M12 9l6 6-6 6" fill="none" stroke="#fff" stroke-width="2.5"/></svg></a>
  <svg class="slide-arrow" style="left:110px" viewBox="0 0 20 34"><path d="M16 3L4 17l12 14" fill="none" stroke="#fff" stroke-width="4"/></svg>
  <div class="thumbs">
    <div class="photo" style="background:linear-gradient(180deg,#4d7fb0,#2d5a6e)" role="img" aria-label="Oceanfront pool at sunset"></div>
    <div class="photo" style="background:linear-gradient(180deg,#6fa0c8,#7a6a4a)" role="img" aria-label="Palm-lined beach villa"></div>
    <div class="photo" style="background:linear-gradient(180deg,#3a4a66,#a07a4a)" role="img" aria-label="Modern home lit at night"></div>
    <div class="photo" style="background:linear-gradient(180deg,#5c6f86,#b88a58)" role="img" aria-label="Illuminated luxury residence"></div>
    <div class="photo active" style="background:linear-gradient(180deg,#2b3a58,#c48a3f)" role="img" aria-label="House with glowing interior at dusk"></div>
    <div class="photo" style="background:linear-gradient(180deg,#23324a,#46607e)" role="img" aria-label="Evening view of a hillside home"></div>
  </div>
  <svg class="slide-arrow" style="left:1070px" viewBox="0 0 20 34"><path d="M4 3l12 14L4 31" fill="none" stroke="#fff" stroke-width="4"/></svg>
</header>

<section class="search">
  <h2>Search Commercial REAL ESTATE LISTINGS</h2>
  <div class="field select" style="left:131px;top:72px;width:397px">Property Type</div>
  <div class="field" style="left:555px;top:72px;width:370px">Type Location or Project or Keyword</div>
  <div class="field select" style="left:131px;top:122px;width:227px">Min Price</div>
  <span class="to">To</span>
  <div class="field select" style="left:415px;top:122px;width:227px">Min Price</div>
  <div class="field select" style="left:713px;top:122px;width:212px">Posted by: All</div>
  <div class="search-btn">Search
    <svg width="14" height="14" viewBox="0 0 14 14"><circle cx="6" cy="6" r="4.5" fill="none" stroke="#fff" stroke-width="2"/><path d="M9.5 9.5L13 13" stroke="#fff" stroke-width="2"/></svg></div>
</section>

<section class="welcome">
  <h1>WELCOME TO MARWICK</h1>
  <div class="tag">ON THE SHORE</div>
  <p>Lorem ipsum dolor sit amet, consectetuer adipiscing elit, sed diam nonummy nibh euismod tincidunt ut laoreet dolore magna aliquam erat volutpat. Ut wisi enim ad minim veniam, quis nostrud exerci tation ullamcorper suscipit lobortis nisl ut aliquip ex ea commodo consequat. Duis autem vel eum iriure dolor in hendrerit in vulputate velit esse molestie consequat, vel illum dolore eu feugiat nulla facilisis at vero eros et accumsan et iusto odio dignissim qui blandit praesent luptatum zzril delenit augue duis dolore te feugait nulla facilisi.</p>
</section>

<section class="featured">
  <h2 class="section-title">Featured Listings</h2>
  <div class="rule"></div>
  <article class="card" style="left:134px">
    <div class="photo" style="background:linear-gradient(180deg,#7fb3e0,#3f8a6a)" role="img" aria-label="Beachfront villa with palm trees"></div>
    <div class="price">$ 1,495,000</div>
    <h3>18420 Tide View</h3><div class="loc">Pacific Coast</div>
    <div class="more">View More</div>
  </article>
  <article class="card" style="left:379px">
    <div class="photo" style="background:linear-gradient(180deg,#4a6a8e,#8c6a4a)" role="img" aria-label="Modern home with pool at twilight"></div>
    <div class="price">$ 1,495,000</div>
    <h3>Lorem ipsum dolor</h3><div class="loc">Pico Blvd</div>
    <div class="more">View More</div>
  </article>
  <article class="card" style="left:615px">
    <div class="photo" style="background:linear-gradient(180deg,#5f95c8,#4a7090)" role="img" aria-label="Contemporary house with lawn and pool"></div>
    <div class="price">$ 1,495,000</div>
    <h3>Lorem ipsum dolor</h3><div class="loc">Pico Blvd</div>
    <div class="more">View More</div>
  </article>
  <article class="card" style="left:857px">
    <div class="photo" style="background:linear-gradient(180deg,#6d9ccc,#9a6a44)" role="img" aria-label="Glass-fronted luxury residence"></div>
    <div class="price">$ 1,495,000</div>
    <h3>Lorem ipsum dolor</h3><div class="loc">Pico Blvd</div>
    <div class="more">View More</div>
  </article>
</section>

<section class="explore">
  <div class="photo" style="left:0;top:0;width:1200px;height:430px;background:linear-gradient(180deg,#1a2538 0%,#2b3b54 50%,#1a1e27 100%)" role="img" aria-label="Coastal home terrace lit at night"></div>
  <h2>EXPLORE ORANGE COUNTY</h2>
  <p>Lorem ipsum dolor sit amet, consectetuer adipiscing elit. Proin nibh augue, suscipit a, scelerisque sed, lacinia in, mi. Cras vel lorem. Etiam pellentesque aliquet tellus. Phasellus pharetra nulla ac diam. Quisque semper justo at risus. Donec venenatis, turpis vel hendrerit interdum, dui ligula ultricies purus, sed posuere libero dui id orci. Nam congue, pede vitae dapibus aliquet, elit magna vulputate arcu, vel tempus metus leo non est.</p>
  <div class="explore-btn">EXPLORE MORE</div>
  <div class="spot" style="left:150px"><div class="tile"><div class="photo" role="img" aria-label="Theme park ride icon"></div></div><span>Larkin Berry Farm</span></div>
  <div class="spot" style="left:308px"><div class="tile"><div class="photo" role="img" aria-label="Castle icon"></div></div><span>Starbright Park</span></div>
  <div class="spot" style="left:481px"><div class="tile"><div class="photo" role="img" aria-label="Stadium icon"></div></div><span>Seraph Field of<br>Anaheim</span></div>
  <div class="spot" style="left:651px"><div class="tile"><div class="photo" role="img" aria-label="Park picnic icon"></div></div><span>Glass Cove State<br>Park</span></div>
  <div class="spot" style="left:821px"><div class="tile"><div class="photo" role="img" aria-label="Zoo animal icon"></div></div><span>Citrus Grove Zoo</span></div>
  <div class="spot" style="left:1003px"><div class="tile"><div class="photo" role="img" aria-label="Surfing icon"></div></div><span>Coastal<br>Surfing Museum</span></div>
</section>

<section class="sold">
  <div class="sold-frame"></div>
  <div class="sold-tab">SOLD PROPERTIES</div>
  <div class="sold-item" style="left:152px">
    <div class="photo" style="background:linear-gradient(180deg,#6a98c4,#3f5f80)" role="img" aria-label="Balcony overlooking the ocean"></div>
    <div class="plus">+</div>
    <div class="info"><span>14207 Pinon c41</span><b>$120548</b></div>
    <div class="status">SOLD OUT</div>
  </div>
  <div class="sold-item" style="left:385px">
    <div class="photo" style="background:linear-gradient(180deg,#3f93c9,#c7a46e)" role="img" aria-label="Resort pool with loungers"></div>
    <div class="plus">+</div>
    <div class="info"><span>14207 Pinon c41</span><b>$120548</b></div>
    <div class="status">SOLD OUT</div>
  </div>
  <div class="sold-item" style="left:615px">
    <div class="photo" style="background:linear-gradient(180deg,#7ab0dc,#4a7a5a)" role="img" aria-label="Villa with palm trees"></div>
    <div class="plus">+</div>
    <div class="info"><span>14207 Pinon c41</span><b>$120548</b></div>
    <div class="status">SOLD OUT</div>
  </div>
  <div class="sold-item" style="left:845px">
    <div class="photo" style="background:linear-gradient(180deg,#8fbce0,#d8d8d0)" role="img" aria-label="White modern house with pool"></div>
    <div class="plus">+</div>
    <div class="info"><span>14207 Pinon c41</span><b>$120548</b></div>
    <div class="status">SOLD OUT</div>
  </div>
</section>

<section class="team">
  <h2 class="section-title">OUR TEAM</h2>
  <div class="rule"></div>
  <div class="bubble bubble-right">Lorem ipsum dolor sit amet, consectetuer adipiscing elit, sed diam nonummy nibh euismod tincidunt ut laoreet dolore magna aliquam erat volutpat. Ut wisi enim ad minim veniam, quis nostrud exerci tation ullamcorper suscipit lobortis.</div>
  <div class="bubble bubble-left">Lorem ipsum dolor sit amet, consectetuer adipiscing elit, sed diam nonummy nibh euismod tincidunt ut laoreet dolore magna aliquam erat volutpat. Ut wisi enim ad minim veniam, quis nostrud exerci tation ullamcorper suscipit lobortis.</div>
  <div class="avatar" style="left:303px;top:370px;background:linear-gradient(180deg,#c9a27a,#8a6a50)" role="img" aria-label="Portrait of Nora Marwick"></div>
  <div class="member" style="left:412px;top:392px">Nora Marwick<small>- Lorem Ipsum Dolor</small></div>
  <div class="avatar" style="left:661px;top:330px;background:linear-gradient(180deg,#8a7a6a,#3a3a44)" role="img" aria-label="Portrait of Glen"></div>
  <div class="member" style="left:774px;top:352px">Glen<small>- Lorem Ipsum Dolor</small></div>
</section>

<section class="consult">
  <div class="photo" style="left:0;top:0;width:1200px;height:301px;background:linear-gradient(90deg,#9fb6cf 0%,#dfe6ee 55%,#b9c9d9 100%)" role="img" aria-label="Smiling agent on the phone in a bright office"></div>
  <svg class="consult-panel" width="700" height="301" viewBox="0 0 700 301">
    <polygon points="0,0 640,0 560,301 0,301" fill="#1f6fc5" opacity=".93"/>
  </svg>
  <h2>REQUEST <b>A CONSULT</b></h2>
  <p>Get started by filling out our online enquiry form. We'll get in touch within <b>24 hours</b></p>
  <div class="consult-icon"><svg width="30" height="22" viewBox="0 0 30 22"><rect x="1" y="1" width="28" height="20" fill="#fff"/><path d="M1 1l14 11L29 1" fill="none" stroke="#8a8f97" stroke-width="2"/></svg></div>
  <div class="input" style="top:20px">Name</div>
  <div class="input" style="top:76px">Email</div>
  <div class="input" style="top:132px">Phone Number</div>
  <div class="input" style="top:188px;height:62px">Your Message</div>
  <div class="send">Send</div>
</section>

<section class="blog">
  <h2 class="section-title">LATEST FROM BLOG</h2>
  <div class="rule"></div>
  <article class="post" style="left:131px">
    <div class="date">FEB<b>28</b></div>
    <div class="ico" style="top:64px"><svg width="20" height="18" viewBox="0 0 20 18"><path d="M10 17S1 11 1 5.5A4.5 4.5 0 0 1 10 3a4.5 4.5 0 0 1 9 2.5C19 11 10 17 10 17z" fill="#fff"/></svg></div>
    <div class="ico" style="top:120px"><svg width="20" height="18" viewBox="0 0 20 18"><path d="M2 2h16v10H8l-4 4v-4H2z" fill="#fff"/></svg></div>
    <div class="photo" style="background:linear-gradient(180deg,#6c8fb4,#4a4e58)" role="img" aria-label="Living room with ocean view"></div>
    <h3>benefits of a reputable cabinet.</h3>
    <div class="meta">MAY 30, 2014 | <b>4 COMMENTS</b> | ♥ 5</div>
    <p>Lorem ipsum dolor sit amet, consectetuer adipiscing elit, sed diam nonummy nibh euismod tincidunt.</p>
    <div class="read">Read More</div>
  </article>
  <article class="post" style="left:451px">
    <div class="date">FEB<b>26</b></div>
    <div class="ico" style="top:64px"><svg width="20" height="18" viewBox="0 0 20 18"><path d="M10 17S1 11 1 5.5A4.5 4.5 0 0 1 10 3a4.5 4.5 0 0 1 9 2.5C19 11 10 17 10 17z" fill="#fff"/></svg></div>
    <div class="ico" style="top:120px"><svg width="20" height="18" viewBox="0 0 20 18"><path d="M2 2h16v10H8l-4 4v-4H2z" fill="#fff"/></svg></div>
    <div class="photo" style="background:linear-gradient(180deg,#3f86c2,#6e4e38)" role="img" aria-label="Infinity pool overlooking the sea"></div>
    <h3>benefits of a reputable cabinet.</h3>
    <div class="meta">MAY 30, 2014 | <b>4 COMMENTS</b> | ♥ 5</div>
    <p>Lorem ipsum dolor sit amet, consectetuer adipiscing elit, sed diam nonummy nibh euismod tincidunt.</p>
    <div class="read">Read More</div>
  </article>
  <article class="post" style="left:771px">
    <div class="date">FEB<b>25</b></div>
    <div class="ico" style="top:64px"><svg width="20" height="18" viewBox="0 0 20 18"><path d="M10 17S1 11 1 5.5A4.5 4.5 0 0 1 10 3a4.5 4.5 0 0 1 9 2.5C19 11 10 17 10 17z" fill="#fff"/></svg></div>
    <div class="ico" style="top:120px"><svg width="20" height="18" viewBox="0 0 20 18"><path d="M2 2h16v10H8l-4 4v-4H2z" fill="#fff"/></svg></div>
    <div class="photo" style="background:linear-gradient(180deg,#2e4a78,#c08a52)" role="img" aria-label="Clifftop home at sunset"></div>
    <h3>benefits of a reputable cabinet.</h3>
    <div class="meta">MAY 30, 2014 | <b>4 COMMENTS</b> | ♥ 5</div>
    <p>Lorem ipsum dolor sit amet, consectetuer adipiscing elit, sed diam nonummy nibh euismod tincidunt.</p>
    <div class="read">Read More</div>
  </article>
</section>

<footer class="site-footer">
  <h4 style="left:131px;top:46px">Quick Links</h4>
  <ul class="links" style="left:131px"><li>Home</li><li>About</li><li>Property Search</li><li>Explore O.C</li></ul>
  <ul class="links" style="left:275px"><li>Team</li><li>Videos</li><li>Blog</li><li>Contact</li></ul>
  <div class="follow">Follow Us On <span></span><span></span><span></span><span></span></div>
  <div class="video-col">
    <h4 style="left:30px;top:64px">Our Video</h4>
    <div class="photo video" style="background:linear-gradient(180deg,#8fb2d4,#5a6a78)" role="img" aria-label="Video still of a modern oceanfront home"></div>
    <div class="play"><svg width="16" height="18" viewBox="0 0 16 18"><path d="M2 1l13 8-13 8z" fill="#fff"/></svg></div>
    <div class="video-bar"><i></i></div>
  </div>
  <h4 style="left:812px;top:46px">Newsletter Signup</h4>
  <p class="news">Lorem ipsum dolor sit amet consectetuer sed diam nibh euismod tincidunt ut laoreet dolore magna.</p>
  <div class="email">Email Address</div>
  <div class="go">GO</div>
</footer>

<div class="copyright">© 2015 Marwick on the Shore. All Rights Reserved.</div>

</body>
</html>
```